CANNABIS BASED BUSINESS CARD DESIGN AND CREATION

WE ARE A PRIVATELY OWNED INVESTMENT CORPORATION. WE PRIMARILY INVEST IN LEGAL PUBLICALLY TRADED CANNABIS COMPANIES THAT ARE TRADED THROUGH THE OTC OR VOLTRIX. WE OFFER THE PUBLIC AN OPPORTUNITY TO PARTICIPATE DIRECTLY WITH THESE COMPANIES FOR NO FEES, NO COMMISSIONS AND IN DEPTH RESEARCH ON EVERY COMPANY PROFILE. WE ARE ALSO PRO FEDERAL LEGALIZATION AND WILL APPLY FOR CULTIVATION AND DISPENSARY LICENSES WHEN THEY BECOME AVAILABLE.

Target Market(s)

30-60 FEMALE AND MALE INVESTORS

Industry/Entity Type

Business

Contact Information for Business Card

EDS CAPITAL GROUP CORPERIN D SLAUGHTER(469) 426-6302ERIN@EDSCAPITALGROUP.COM

Font styles to use
Decorative

Requirements
Must have
• COMPANY LOGO
• CANNABIS LOGO
Nice to have
• MODERN FONT AND LOGOS

```html
<!DOCTYPE html>
<html lang="en">
<head>
<meta charset="utf-8">
<title>TQM Capital Group Corp – Business Card</title>
<link rel="stylesheet" href="https://fonts.googleapis.com/css2?family=Lato:wght@400;700&display=swap">
<style>
  :root {
    --backdrop: #5f6b12;
    --card: #0b0b0b;
    --card-edge: #1b1b1b;
    --leaf-green: #2fae4a;
    --emblem-tone: rgba(255,255,255,0.07);
    --text-white: #ffffff;
    --text-grey: #b9b9b9;
    --rule: #3a3a3a;
  }
  html, body {
    margin: 0;
    width: 1200px;
    height: 900px;
    overflow: hidden;
    background: var(--backdrop);
    font-family: "Lato", sans-serif;
  }
  .stage { position: relative; width: 1200px; height: 900px; }
  .card {
    position: absolute;
    width: 640px;
    height: 366px;
    border-radius: 22px;
    background: linear-gradient(135deg, var(--card-edge) 0%, var(--card) 55%);
    box-shadow: 0 10px 30px rgba(0,0,0,0.35);
    overflow: hidden;
  }
  .card-front { left: 280px; top: 56px; }
  .card-back  { left: 280px; top: 478px; }

  .faint-emblem {
    position: absolute;
    right: -10px;
    top: -30px;
    width: 340px;
    height: 340px;
    border-radius: 50%;
    background: radial-gradient(circle at 50% 50%, var(--emblem-tone) 0%, rgba(255,255,255,0.04) 45%, rgba(255,255,255,0) 70%);
  }

  .brand {
    display: flex;
    align-items: center;
    gap: 12px;
    color: var(--text-white);
    font-weight: 700;
    letter-spacing: 1px;
    white-space: nowrap;
  }
  .brand-dot {
    width: 16px;
    height: 16px;
    border-radius: 50%;
    background: var(--leaf-green);
    flex: none;
  }
  .card-front .brand {
    position: absolute;
    left: 0; right: 0;
    top: 164px;
    justify-content: center;
    font-size: 30px;
  }
  .card-back .brand {
    position: absolute;
    right: 40px;
    top: 62px;
    font-size: 19px;
  }
  .card-back .brand-dot { width: 12px; height: 12px; }

  .contact-rule {
    position: absolute;
    right: 40px;
    top: 150px;
    width: 250px;
    height: 1px;
    background: var(--rule);
  }
  .contact-list {
    position: absolute;
    right: 40px;
    top: 168px;
    width: 250px;
    margin: 0;
    padding: 0;
    list-style: none;
  }
  .contact-item {
    display: flex;
    align-items: center;
    gap: 10px;
    color: var(--text-grey);
    font-size: 13px;
    line-height: 26px;
    white-space: nowrap;
  }
  .contact-icon { width: 14px; height: 14px; flex: none; }

  .holder-name {
    position: absolute;
    left: 40px;
    top: 270px;
    margin: 0;
    color: var(--text-white);
    font-size: 17px;
    font-weight: 400;
    letter-spacing: 0.5px;
  }
  .holder-rule {
    position: absolute;
    left: 40px;
    top: 302px;
    width: 250px;
    height: 1px;
    background: var(--rule);
  }
</style>
</head>
<body>
<main class="stage">
  <section class="card card-front" aria-label="Card front">
    <div class="faint-emblem" role="img" aria-label="Faint large leaf emblem watermark in the top right"></div>
    <div class="brand"><span class="brand-dot"></span>TQM CAPITAL GROUP CORP</div>
  </section>

  <section class="card card-back" aria-label="Card back">
    <div class="brand"><span class="brand-dot"></span>TQM CAPITAL GROUP CORP</div>
    <div class="contact-rule"></div>
    <ul class="contact-list">
      <li class="contact-item">
        <svg class="contact-icon" viewBox="0 0 24 24" aria-hidden="true"><path fill="#2fae4a" d="M6.6 10.8a15 15 0 0 0 6.6 6.6l2.2-2.2c.3-.3.7-.4 1-.2 1.1.4 2.3.6 3.6.6.6 0 1 .4 1 1V20c0 .6-.4 1-1 1A17 17 0 0 1 3 4c0-.6.4-1 1-1h3.5c.6 0 1 .4 1 1 0 1.3.2 2.5.6 3.6.1.3 0 .7-.2 1z"/></svg>
        (555) 013-4478
      </li>
      <li class="contact-item">
        <svg class="contact-icon" viewBox="0 0 24 24" aria-hidden="true"><rect x="2" y="5" width="20" height="14" rx="2" fill="#2fae4a"/><path d="M3 6l9 7 9-7" stroke="#0b0b0b" stroke-width="2" fill="none"/></svg>
        marla@tqmcapitalgroup-demo.com
      </li>
      <li class="contact-item">
        <svg class="contact-icon" viewBox="0 0 24 24" aria-hidden="true"><path d="M10 14a4 4 0 0 0 5.7 0l3-3a4 4 0 0 0-5.7-5.7l-1 1M14 10a4 4 0 0 0-5.7 0l-3 3a4 4 0 0 0 5.7 5.7l1-1" stroke="#2fae4a" stroke-width="2.4" fill="none" stroke-linecap="round"/></svg>
        www.tqmcapitalgroup-demo.com
      </li>
    </ul>
    <h2 class="holder-name">MARLA J PENDLEBURY</h2>
    <div class="holder-rule"></div>
  </section>
</main>
</body>
</html>
```